sydney wedding photography business needs a business card design

we need a business card design for a sydney based wedding photography and videography business. our business name is :golden hour studio and film. our target clients are 24-35 yrs female. our style is candid, organic, natural, dynamic. we are a team of young photographers and videographers, and help brides to create memories that they will cherish for the rest of their lives. the logo will be provided. we want an elegant design that reflects our style, and also want to give a great impression to our clients that we are one of the best studios in sydney and our brand means quality and premium service.

Target Market(s)

bride to be, 24-35 years old, living in sydney and surrunding areas

Industry/Entity Type

Wedding Photography

Contact Information for Business Card

address: 57 tarrant street, glenmore nsw 2047
mobile: 0431872259
phone: (02) 9163 2408
info@tidewillowstudio.net.au
www.tidewillowstudio.net.au
facebook:tidewillowweddings
instagram:tidewillowweddings

Font styles to use
Serif
Sans Serif

Requirements
Nice to have
• maybe add my slogan"memories beyond eternity" if the layout looks good
Should not have
• no black color, not good idea for wedding biz card

```html
<!DOCTYPE html>
<html lang="en">
<head>
<meta charset="utf-8">
<title>Golden Hour Studio and Film – Business Card</title>
<link rel="stylesheet" href="https://fonts.googleapis.com/css2?family=Montserrat:wght@400;500&display=swap">
<style>
  :root {
    --page: #ece6dd;
    --card-mocha: #4a3b31;
    --card-mocha-2: #5e4b3e;
    --gold: #e2bd4a;
    --gold-soft: #d6b04a;
    --icon-ink: #4a3b31;
    --text-light: #f6efe6;
    --photo-top: #6b5646;
    --photo-bottom: #3f3229;
  }
  * { margin: 0; padding: 0; box-sizing: border-box; }
  html, body {
    width: 1200px; height: 892px; overflow: hidden;
    background: var(--page);
    font-family: "Montserrat", Arial, sans-serif;
  }
  .canvas {
    position: relative; width: 1200px; height: 892px;
    display: flex; flex-direction: column; align-items: center; justify-content: center; gap: 36px;
  }
  .card {
    position: relative; width: 700px; height: 400px;
    border-radius: 4px; overflow: hidden;
    box-shadow: 0 10px 30px rgba(60,40,25,0.25);
  }
  .card-front {
    background: linear-gradient(160deg, var(--card-mocha-2), var(--card-mocha));
    display: flex; align-items: center; justify-content: center;
  }
  .brand-name {
    color: var(--gold);
    font-weight: 500;
    font-size: 34px;
    letter-spacing: 6px;
    text-transform: uppercase;
    text-align: center;
    line-height: 1.3;
  }
  .card-back { background: var(--card-mocha); }
  .card-photo {
    position: absolute; inset: 0;
    background: linear-gradient(200deg, var(--photo-top) 0%, #574638 45%, var(--photo-bottom) 100%);
  }
  .card-back .brand-name {
    position: absolute; right: 40px; top: 70px;
    font-size: 24px; letter-spacing: 4px; text-align: right;
  }
  .contact-list {
    position: absolute; left: 40px; bottom: 46px;
    list-style: none;
  }
  .contact-item {
    display: flex; align-items: center; gap: 12px;
    color: var(--text-light); font-size: 15px; font-weight: 400; line-height: 1;
    margin-top: 9px;
  }
  .contact-icon {
    width: 18px; height: 18px; background: var(--gold-soft);
    display: flex; align-items: center; justify-content: center; flex: none;
  }
  .contact-icon svg { width: 12px; height: 12px; }
</style>
</head>
<body>
<main class="canvas">
  <section class="card card-front">
    <p class="brand-name">Golden Hour<br>Studio and Film</p>
  </section>

  <section class="card card-back">
    <div class="card-photo" role="img" aria-label="Warm toned wedding photograph of a couple in a panelled room"></div>
    <p class="brand-name">Golden Hour<br>Studio and Film</p>
    <ul class="contact-list">
      <li class="contact-item">
        <span class="contact-icon"><svg viewBox="0 0 12 12"><path d="M2 1 L4.5 1 L5.2 3.5 L3.8 4.5 Q4.8 6.8 7.5 8.2 L8.5 6.8 L11 7.5 L11 10 Q6 11 3 8 Q1 5 2 1Z" fill="#4a3b31"/></svg></span>
        (02) 9163 2408
      </li>
      <li class="contact-item">
        <span class="contact-icon"><svg viewBox="0 0 12 12"><rect x="3.5" y="1" width="5" height="10" rx="1" fill="#4a3b31"/><rect x="4.5" y="2.2" width="3" height="6" fill="#d6b04a"/></svg></span>
        0431872259
      </li>
      <li class="contact-item">
        <span class="contact-icon"><svg viewBox="0 0 12 12"><circle cx="6" cy="6" r="4.5" fill="none" stroke="#4a3b31" stroke-width="1.2"/><path d="M1.5 6 H10.5 M6 1.5 Q3.5 6 6 10.5 M6 1.5 Q8.5 6 6 10.5" fill="none" stroke="#4a3b31" stroke-width="1"/></svg></span>
        www.tidewillowstudio.net.au
      </li>
      <li class="contact-item">
        <span class="contact-icon"><svg viewBox="0 0 12 12"><rect x="1.5" y="3" width="9" height="6.5" fill="none" stroke="#4a3b31" stroke-width="1.2"/><path d="M1.5 3 L6 7 L10.5 3" fill="none" stroke="#4a3b31" stroke-width="1.2"/></svg></span>
        info@tidewillowstudio.net.au
      </li>
      <li class="contact-item">
        <span class="contact-icon"><svg viewBox="0 0 12 12"><rect x="3" y="3" width="6" height="6" fill="#4a3b31"/></svg></span>
        tidewillowweddings
      </li>
      <li class="contact-item">
        <span class="contact-icon"><svg viewBox="0 0 12 12"><circle cx="6" cy="6" r="3" fill="#4a3b31"/></svg></span>
        tidewillowweddings
      </li>
      <li class="contact-item">
        <span class="contact-icon"><svg viewBox="0 0 12 12"><path d="M6 11 Q2 6.5 2 4.5 A4 4 0 0 1 10 4.5 Q10 6.5 6 11Z" fill="#4a3b31"/><circle cx="6" cy="4.5" r="1.4" fill="#d6b04a"/></svg></span>
        57 tarrant street, glenmore nsw 2047
      </li>
    </ul>
  </section>
</main>
</body>
</html>
```